I have a logo and need to design the business card and stationery.
Updates

The uploaded logo image named as GREYMARSH CONSTRUCTION which is to be replaced to GREYMARSH CONTRACTS. Kindly add below details and submit the designs- Company name- Greymarsh Engineering Contracts LLP Name & Post- Kelvan Joshi (Designated Partner) Address- Block No.317, Wing C, Tulvo Trade Court, Manek Pural Road, Ruparel Industrial Estate, Goregaon(E), Mumbai - 400 063 Contact- +91 97415 60382 Email- kelvanjoshi@mailbrook.example Website- www.greymarshcontracts.example Contact for Letterhead- +91-22-28754193

Hi Tovin Rahul, We are liking your Design #28860835. We have suggested some changes which are mentioned in feedback. Kindly revert with it asap to finalize this design.

Colors

Designer to choose colors to be used in the design.

```html
<!DOCTYPE html>
<html lang="en">
<head>
<meta charset="utf-8">
<title>Greymarsh Contracts – Business Card</title>
<link rel="stylesheet" href="https://fonts.googleapis.com/css2?family=Michroma&family=Roboto:wght@400;500&display=swap">
<style>
  :root {
    --backdrop: #d9d8d5;
    --card: #333333;
    --card-edge: #2a2a2a;
    --ink: #ffffff;
    --ink-soft: #e6e6e6;
    --rule: #cfcfcf;
    --mark-back: #8c8c8c;
  }
  * { margin: 0; padding: 0; box-sizing: border-box; }
  html, body { width: 1200px; height: 801px; overflow: hidden; }
  body {
    background: var(--backdrop);
    display: flex;
    align-items: center;
    justify-content: center;
    gap: 48px;
    font-family: "Roboto", Arial, sans-serif;
  }
  .card {
    width: 520px;
    height: 297px;
    background: var(--card);
    border: 1px solid var(--card-edge);
    position: relative;
    color: var(--ink);
  }
  /* Front */
  .card-front { display: flex; align-items: center; }
  .brand {
    width: 250px;
    display: flex;
    align-items: center;
    justify-content: center;
    gap: 12px;
  }
  .brand-square {
    width: 34px; height: 34px;
    background: var(--ink);
    flex: none;
  }
  .brand-name {
    font-family: "Michroma", Arial, sans-serif;
    font-size: 15px;
    line-height: 1.35;
    color: var(--ink);
    letter-spacing: 0.5px;
  }
  .divider {
    width: 1px;
    height: 170px;
    background: var(--rule);
  }
  .details { padding-left: 20px; }
  .person-name {
    font-family: "Michroma", Arial, sans-serif;
    font-size: 15px;
    font-weight: 400;
    letter-spacing: 0.5px;
  }
  .person-title {
    font-size: 13px;
    color: var(--ink-soft);
    margin-top: 2px;
    margin-bottom: 12px;
  }
  .contact-list { list-style: none; font-size: 10.5px; line-height: 1.55; }
  .contact-list li { display: flex; align-items: center; gap: 6px; }
  .contact-list svg { width: 10px; height: 10px; flex: none; }
  .address {
    font-style: normal;
    font-size: 10.5px;
    line-height: 1.5;
    margin-top: 9px;
    color: var(--ink-soft);
  }
  /* Back */
  .card-back {
    display: flex;
    align-items: center;
    justify-content: center;
    gap: 16px;
  }
  .card-back .brand-square { width: 48px; height: 48px; background: var(--mark-back); }
  .card-back .brand-name { font-size: 21px; color: var(--mark-back); }
</style>
</head>
<body>
  <section class="card card-front" aria-label="Business card front">
    <div class="brand">
      <span class="brand-square" aria-hidden="true"></span>
      <div class="brand-name">GREYMARSH<br>CONTRACTS</div>
    </div>
    <div class="divider"></div>
    <div class="details">
      <h1 class="person-name">KELVAN JOSHI</h1>
      <p class="person-title">Designated Partner</p>
      <ul class="contact-list">
        <li>
          <svg viewBox="0 0 10 10" aria-hidden="true"><path d="M2 1 L4 1 L4.6 3 L3.4 3.8 Q4.4 5.8 6.2 6.6 L7 5.4 L9 6 L9 8 Q9 9 8 9 Q1 8.4 1 2 Q1 1 2 1 Z" fill="#fff"/></svg>
          +91 97415 60382
        </li>
        <li>
          <svg viewBox="0 0 10 10" aria-hidden="true"><path d="M2 1 L4 1 L4.6 3 L3.4 3.8 Q4.4 5.8 6.2 6.6 L7 5.4 L9 6 L9 8 Q9 9 8 9 Q1 8.4 1 2 Q1 1 2 1 Z" fill="#fff"/></svg>
          +91-22-28754193
        </li>
        <li>
          <svg viewBox="0 0 10 10" aria-hidden="true"><rect x="0.5" y="2" width="9" height="6" fill="#fff"/><path d="M0.5 2 L5 5.5 L9.5 2" stroke="#333" stroke-width="0.9" fill="none"/></svg>
          kelvanjoshi@mailbrook.example
        </li>
        <li>
          <svg viewBox="0 0 10 10" aria-hidden="true"><rect x="0.5" y="2" width="9" height="6" fill="#fff"/><path d="M0.5 2 L5 5.5 L9.5 2" stroke="#333" stroke-width="0.9" fill="none"/></svg>
          info@greymarshcontracts.example
        </li>
        <li>
          <svg viewBox="0 0 10 10" aria-hidden="true"><circle cx="5" cy="5" r="4.5" fill="#fff"/><ellipse cx="5" cy="5" rx="1.8" ry="4.5" stroke="#333" stroke-width="0.7" fill="none"/><line x1="0.5" y1="5" x2="9.5" y2="5" stroke="#333" stroke-width="0.7"/></svg>
          www.greymarshcontracts.example
        </li>
      </ul>
      <address class="address">
        Greymarsh Engineering Contracts LLP<br>
        Block No.317, Wing C, Tulvo Trade Court,<br>
        Manek Pural Road, Ruparel Industrial Estate,<br>
        Goregaon(E), Mumbai - 400 063
      </address>
    </div>
  </section>

  <section class="card card-back" aria-label="Business card back">
    <span class="brand-square" aria-hidden="true"></span>
    <div class="brand-name">GREYMARSH<br>CONTRACTS</div>
  </section>
</body>
</html>
```